Dorla's Cleaners new delivery postcard

We need to advertise for our new pick up and delivery dry cleaning/laundry service.
Mens Business Shirts $2.00
Pants $4.50
Skirts $5.00
Dry Clean Shirt/Blouse $5.00
Dress $9.00
2 Piece Suits $9.00
Updates
We would like to use a 5x7 size postcard, printed on both sides. We would like to add a discount to the card for 25% off of their first order, with the flyer.
We are a famly run dry cleaners. My name is Rosalind Tupper and my cell # is 614-302-7781. We are trying to expand our business to include free pick and delivery.
If possible can you use the logo I sent some where on the postcard? The phone # for the store is 614-295-3064.
Reason: Still need to get partners approval.

```html
<!DOCTYPE html>
<html lang="en">
<head>
<meta charset="utf-8">
<title>Dorla's Cleaners – Free Delivery &amp; Pick up</title>
<link rel="stylesheet" href="https://fonts.googleapis.com/css2?family=Alfa+Slab+One&family=Fredoka:wght@600;700&family=Londrina+Solid:wght@900&display=swap">
<style>
  :root {
    --sky-light: #eaf7fd;
    --sky-mid: #a9dcf3;
    --sky-deep: #5fb8e6;
    --panel-blue: #2f8fd3;
    --panel-blue-deep: #1f78c2;
    --accent-green: #5dbb2e;
    --brand-teal: #1aa3d8;
    --ink-navy: #17315c;
    --phone-blue: #1d5aa3;
    --service-yellow: #f7e31b;
    --paper-grey: #eceff2;
    --white: #ffffff;
  }
  * { margin: 0; padding: 0; box-sizing: border-box; }
  html, body { width: 1200px; height: 856px; overflow: hidden; background: var(--white); }
  .postcard { position: relative; width: 1200px; height: 856px; overflow: hidden; }

  .bubble-backdrop {
    position: absolute; inset: 0;
    background:
      radial-gradient(ellipse 520px 360px at 560px 180px, rgba(255,255,255,0.95), rgba(255,255,255,0) 70%),
      radial-gradient(ellipse 600px 220px at 300px 560px, rgba(255,255,255,0.55), rgba(255,255,255,0) 70%),
      linear-gradient(180deg, var(--sky-mid) 0%, var(--sky-light) 40%, var(--sky-deep) 100%);
  }
  .panel-shapes { position: absolute; inset: 0; }

  .brand-mark {
    position: absolute; left: 40px; top: 40px;
    width: 124px; height: 124px; border-radius: 50%;
    background: var(--ink-navy);
  }
  .brand-name {
    position: absolute; left: 180px; top: 62px;
    font-family: "Alfa Slab One", serif; font-size: 58px; line-height: 1;
    color: var(--brand-teal); letter-spacing: 1px;
  }
  .service-list {
    position: absolute; left: 180px; top: 134px; width: 740px;
    font-family: "Londrina Solid", sans-serif; font-weight: 900;
    font-size: 31px; line-height: 40px; text-align: center;
    color: var(--service-yellow);
    text-shadow: -2px -2px 0 var(--ink-navy), 2px -2px 0 var(--ink-navy), -2px 2px 0 var(--ink-navy), 2px 2px 0 var(--ink-navy), 0 3px 0 var(--ink-navy);
  }
  .outlined {
    font-family: "Fredoka", sans-serif; font-weight: 700;
    text-shadow: -3px -3px 0 var(--white), 3px -3px 0 var(--white), -3px 3px 0 var(--white), 3px 3px 0 var(--white), 0 4px 0 var(--white), 4px 0 0 var(--white), -4px 0 0 var(--white), 0 -4px 0 var(--white);
  }
  .offer-headline {
    position: absolute; left: 110px; top: 300px; width: 780px;
    font-size: 60px; line-height: 1; text-align: center; color: var(--phone-blue);
  }
  .offer-headline .highlight { color: var(--accent-green); }
  .call-label {
    position: absolute; left: 76px; top: 490px;
    font-family: "Fredoka", sans-serif; font-weight: 700; font-size: 56px; line-height: 1;
    color: var(--white);
    text-shadow: -3px -3px 0 var(--phone-blue), 3px -3px 0 var(--phone-blue), -3px 3px 0 var(--phone-blue), 3px 3px 0 var(--phone-blue), 0 4px 0 var(--phone-blue);
  }
  .store-phone {
    position: absolute; left: 112px; top: 550px;
    font-size: 94px; line-height: 1; color: var(--phone-blue); letter-spacing: 1px;
  }
</style>
</head>
<body>
<main class="postcard">
  <div class="bubble-backdrop" role="img" aria-label="Soap bubbles floating over clear blue water"></div>

  <svg class="panel-shapes" viewBox="0 0 1200 856" width="1200" height="856" aria-hidden="true">
    <defs>
      <linearGradient id="panelFill" x1="0" y1="0" x2="0" y2="1">
        <stop offset="0" stop-color="#3c9ad9"/>
        <stop offset="1" stop-color="#1f78c2"/>
      </linearGradient>
      <radialGradient id="bubbleGlow" cx="0.75" cy="0.65" r="0.5">
        <stop offset="0" stop-color="#bfe7fb" stop-opacity="0.85"/>
        <stop offset="1" stop-color="#bfe7fb" stop-opacity="0"/>
      </radialGradient>
      <linearGradient id="paperFill" x1="0" y1="0" x2="0" y2="1">
        <stop offset="0" stop-color="#ffffff"/>
        <stop offset="1" stop-color="#dfe3e8"/>
      </linearGradient>
    </defs>
    <path class="blue-panel" d="M937,0 C905,260 850,520 540,630 C330,700 150,712 0,706 L0,856 L1200,856 L1200,0 Z" fill="url(#panelFill)"/>
    <rect class="panel-bubbles" x="820" y="0" width="380" height="760" fill="url(#bubbleGlow)" role="img" aria-label="Cluster of soap bubbles"/>
    <path class="accent-curve" d="M937,0 C905,260 850,520 540,630 C330,700 150,712 0,706" fill="none" stroke="var(--accent-green)" stroke-width="9"/>
    <path class="paper-band" d="M0,772 C380,786 860,808 1200,836 L1200,856 L0,856 Z" fill="url(#paperFill)"/>
  </svg>

  <div class="brand-mark" aria-hidden="true"></div>
  <h1 class="brand-name">DORLA'S CLEANERS</h1>
  <p class="service-list">•Dry cleaning •Shirt laundry •Alterations<br>•Wedding dresses •Storage</p>

  <h2 class="offer-headline outlined"><span class="highlight">Free</span> Delivery &amp; Pick up</h2>

  <p class="call-label">Call NOW</p>
  <p class="store-phone outlined">614-295-3064</p>
</main>
</body>
</html>
```